Birchline Septic Solutions

Would like to see some single sided ones but would also like to see some double sided with one sided only being the logo. Owners name is Colin Vandro. Phone number is 555-214-0387
Services are pumping, inspections, installs, and repairs

Contact Information for Business Card

555-241-0387 Colin Vandro Maplebrook, OH

```html
<!DOCTYPE html>
<html lang="en">
<head>
<meta charset="utf-8">
<title>Birchline Septic Solutions – Business Cards</title>
<link href="https://fonts.googleapis.com/css2?family=Montserrat:wght@400;500;700;800&display=swap" rel="stylesheet">
<style>
  :root {
    --backdrop: #4a4a4a;
    --card-black: #171717;
    --teal: #2dbdb6;
    --white: #ffffff;
  }
  * { box-sizing: border-box; margin: 0; padding: 0; }
  html, body {
    width: 1200px; height: 801px; overflow: hidden;
    background: var(--backdrop);
    font-family: "Montserrat", Arial, sans-serif;
  }
  .sheet {
    position: relative; width: 1200px; height: 801px;
    display: flex; align-items: center; justify-content: center; gap: 60px;
  }
  .card {
    position: relative; width: 520px; height: 297px;
    background: var(--card-black); overflow: hidden;
    box-shadow: 0 10px 24px rgba(0,0,0,.35);
  }
  .wordmark {
    color: var(--white); font-weight: 800; text-transform: uppercase;
    line-height: 1; text-align: center;
  }
  .wordmark .wordmark-main { display: block; }
  .wordmark .wordmark-sub { display: block; }

  /* Front */
  .card-front .wordmark {
    position: absolute; left: 0; right: 0; top: 78px;
  }
  .card-front .wordmark-main { font-size: 50px; letter-spacing: 2px; }
  .card-front .wordmark-sub { font-size: 19px; letter-spacing: 6px; margin-top: 12px; }
  .services-band {
    position: absolute; left: 0; right: 0; top: 226px; height: 30px;
    background: var(--teal); color: var(--white);
    font-size: 15.5px; font-weight: 500;
    display: flex; align-items: center; justify-content: center;
  }

  /* Back */
  .card-back .swoosh { position: absolute; inset: 0; }
  .card-back .wordmark {
    position: absolute; left: 22px; width: 218px; top: 108px;
  }
  .card-back .wordmark-main { font-size: 33px; letter-spacing: 1px; }
  .card-back .wordmark-sub { font-size: 12px; letter-spacing: 3.5px; margin-top: 8px; }
  .divider {
    position: absolute; left: 262px; top: 24px; width: 1.5px; height: 168px;
    background: var(--teal);
  }
  .contact {
    position: absolute; left: 282px; top: 22px; color: var(--white);
  }
  .contact-name { color: var(--teal); font-weight: 700; font-size: 21px; }
  .contact-town { font-size: 12px; margin-top: 1px; }
  .contact-list { list-style: none; margin-top: 16px; font-size: 12.5px; }
  .contact-list li { display: flex; align-items: center; gap: 8px; height: 17px; }
  .contact-list svg { width: 10px; height: 10px; flex: none; }
  .contact-address { font-size: 12.5px; margin-top: 14px; line-height: 1.35; }
</style>
</head>
<body>
<main class="sheet">

  <section class="card card-front" aria-label="Business card front">
    <h1 class="wordmark">
      <span class="wordmark-main">Birchline</span>
      <span class="wordmark-sub">Septic Solutions</span>
    </h1>
    <p class="services-band">Services are pumping, inspections, installs, and repairs</p>
  </section>

  <section class="card card-back" aria-label="Business card back">
    <svg class="swoosh" viewBox="0 0 520 297" preserveAspectRatio="none" aria-hidden="true">
      <path d="M40 297 C 210 250, 390 225, 520 200 L520 214 C 400 238, 230 262, 90 297 Z" fill="var(--teal)"/>
      <path d="M175 297 C 300 262, 420 238, 520 222 L520 297 Z" fill="var(--white)"/>
    </svg>
    <h2 class="wordmark">
      <span class="wordmark-main">Birchline</span>
      <span class="wordmark-sub">Septic Solutions</span>
    </h2>
    <div class="divider"></div>
    <div class="contact">
      <p class="contact-name">Colin Vandro</p>
      <p class="contact-town">Maplebrook</p>
      <ul class="contact-list">
        <li>
          <svg viewBox="0 0 10 10"><path d="M2 1 L4 1 L4.6 3 L3.5 3.8 C4 5 5 6 6.2 6.5 L7 5.4 L9 6 L9 8 C5 8.5 1.5 5 2 1 Z" fill="var(--teal)"/></svg>
          555-214-0387
        </li>
        <li>
          <svg viewBox="0 0 10 10"><rect x="0.5" y="2" width="9" height="6.5" fill="var(--teal)"/><path d="M0.5 2 L5 5.5 L9.5 2" stroke="var(--card-black)" stroke-width="0.9" fill="none"/></svg>
          info@yourgmail.com
        </li>
        <li>
          <svg viewBox="0 0 10 10"><circle cx="5" cy="5" r="4.5" fill="var(--teal)"/><path d="M0.5 5 H9.5 M5 0.5 C3 3 3 7 5 9.5 M5 0.5 C7 3 7 7 5 9.5" stroke="var(--card-black)" stroke-width="0.7" fill="none"/></svg>
          www.yourwebsite.com
        </li>
      </ul>
      <p class="contact-address">Your address, City<br>State, Zip 1234</p>
    </div>
  </section>

</main>
</body>
</html>
```